KRL Stationery Design Project

Dear Designers,
We need a new stationery design for company to match our new logo.
Designers should provide a design for the following:
1. Business Card: 3.5x2 Inches.
2. Letterhead: A4 size.
3. Envelops: 25x35.5 Cm.
You can keep the Arabic name at the bottom of the logo Or you can use the separate attached Arabic Name.
Please refer to the attached logo guide for design information.
Sample Business Card information:
Name: Tarek Sowan
Position: Operation Manager
Tel: +966 920007164 Ex. 500
Fax: +966 (3)8842617
Mob: +966 (5)00263817
email: tarek@krl-example.com.sa
URL: www.krl-example.com.sa
Address:
Nakheel Heights, Suite 718
Zayed bin Omar Str.
Khobar, 31847
Saudi Arabia
Updates
Dear All,
Please note, we had uploaded our logo along with Arabic writing in Adobe illustrator format (.ai).
Regards,
Karim
Dear All,
A sample data for the business card had been added as per your request.
Regards,
Karim

```html
<!DOCTYPE html>
<html lang="en">
<head>
<meta charset="utf-8">
<title>KRL Business Card</title>
<link rel="stylesheet" href="https://fonts.googleapis.com/css2?family=Open+Sans:wght@400;600;700;800&family=Cairo:wght@700&display=swap">
<style>
  :root {
    --navy: #0f3c60;
    --navy-deep: #0b3152;
    --paper: #ffffff;
    --silver: #a9acae;
    --ink-light: #f1f4f7;
    --backdrop: #d9dee2;
  }
  * { box-sizing: border-box; margin: 0; padding: 0; }
  html, body { width: 1200px; height: 960px; overflow: hidden; }
  body {
    background: var(--backdrop);
    font-family: "Open Sans", Arial, sans-serif;
    display: flex;
    flex-direction: column;
    align-items: center;
    justify-content: center;
    gap: 60px;
  }
  .card {
    position: relative;
    width: 700px;
    height: 400px;
    overflow: hidden;
    box-shadow: 0 6px 18px rgba(0,0,0,0.18);
  }

  /* Front */
  .card-front { background: var(--navy); }
  .front-band { position: absolute; inset: 0; width: 100%; height: 100%; }
  .brand {
    position: absolute;
    left: 0; right: 0; top: 38px;
    text-align: center;
  }
  .brand-name {
    font-weight: 800;
    font-size: 64px;
    line-height: 1;
    letter-spacing: 2px;
    color: var(--navy);
  }
  .brand-arabic {
    font-family: "Cairo", "Open Sans", sans-serif;
    font-weight: 700;
    font-size: 26px;
    color: var(--navy);
    margin-top: 8px;
    direction: rtl;
  }
  .person {
    position: absolute;
    left: 0; right: 0; top: 196px;
    text-align: center;
    color: var(--ink-light);
  }
  .person-name { font-size: 24px; font-weight: 400; }
  .person-role { font-size: 14px; margin-top: 4px; }
  .address {
    position: absolute;
    right: 390px; top: 278px;
    text-align: right;
    color: var(--ink-light);
    font-size: 15px;
    line-height: 22px;
    font-style: normal;
  }
  .contacts {
    position: absolute;
    left: 340px; top: 262px;
    list-style: none;
    color: var(--ink-light);
    font-size: 14.5px;
    line-height: 23px;
  }
  .contacts li { display: flex; align-items: center; gap: 10px; }
  .contacts svg { width: 13px; height: 13px; fill: var(--ink-light); flex: none; }

  /* Back */
  .card-back {
    background: var(--navy-deep);
    display: flex;
    flex-direction: column;
    align-items: center;
    justify-content: center;
  }
  .back-name {
    font-weight: 800;
    font-size: 110px;
    line-height: 1;
    letter-spacing: 4px;
    color: var(--paper);
    margin-top: -30px;
  }
  .back-url {
    position: absolute;
    bottom: 46px;
    left: 0; right: 0;
    text-align: center;
    color: var(--ink-light);
    font-weight: 700;
    font-size: 14px;
    letter-spacing: 1px;
  }
</style>
</head>
<body>

<section class="card card-front">
  <svg class="front-band" viewBox="0 0 700 400" preserveAspectRatio="none" aria-hidden="true">
    <polygon points="0,0 700,0 700,148 0,190" fill="#ffffff"/>
    <polygon points="0,190 700,148 700,158 0,200" fill="#a9acae"/>
    <polygon points="0,200 700,158 700,164 0,206" fill="#ffffff"/>
  </svg>

  <header class="brand">
    <div class="brand-name">KRL</div>
    <div class="brand-arabic" lang="ar">كي آر إل</div>
  </header>

  <div class="person">
    <div class="person-name">Tarek Sowan</div>
    <div class="person-role">Operation Manager</div>
  </div>

  <address class="address">
    Nakheel Heights, Suite 718<br>
    Zayed bin Omar Str.,<br>
    Khobar, 31847,<br>
    Saudi Arabia
  </address>

  <ul class="contacts">
    <li>
      <svg viewBox="0 0 16 16" aria-label="Phone"><path d="M3 1l3 3-1.5 2c1 2 3 4 5 5L11.5 9.5l3 3-2 2.5C6 14 2 10 1 3.5z"/></svg>
      +966 920007164 Ex. 500
    </li>
    <li>
      <svg viewBox="0 0 16 16" aria-label="Fax"><path d="M4 1h7v4H4zM1 6h14v7h-3v2H4v-2H1zm4 5v3h6v-3z"/></svg>
      +966 (3)8842617
    </li>
    <li>
      <svg viewBox="0 0 16 16" aria-label="Mobile"><path d="M4 0h8v16H4zm1.5 2v9h5V2zM7 13v1.5h2V13z"/></svg>
      +966 (5)00263817
    </li>
    <li>
      <svg viewBox="0 0 16 16" aria-label="Email"><path d="M1 6l7-5 7 5v9H1zm1.5 1.2V13.5h11V7.2L8 11z"/></svg>
      tarek@krl-example.com.sa
    </li>
  </ul>
</section>

<section class="card card-back">
  <div class="back-name">KRL</div>
  <div class="back-url">www.krl-example.com.sa</div>
</section>

</body>
</html>
```